Create modern and sleek business card for luxury real estate company

We're a "boutique" real estate office looking for a design that gets across a highly modern luxury brand. Blacks and whites are probably the best colors unless we try a silver foil for the logo. I've attached a version of our current logo here. I'd like to swap out the current font on there with Gotham Light Regular.

I'm looking to have one side of the card have the logo with the space for our agents info on the other side.

Target Market(s)

Young professionals in a "luxury" headspace

Industry/Entity Type

Real estate

Contact Information for Business Card

A place for agent name, cell number, website. The slogan "Quietly Redefining Fine Homes".

Font styles to use
Other font styles liked:
• Gotham Regular

Colors

Designer to choose only greyscale colors for use in the design.

Requirements
Must have
• Matte black as the background color. Clean lines and use of contrast. A specific design aspect that will use silver foil.
Nice to have
• Up in the air on integrating a QR code
Should not have
• Any houses or other real estate related design (ex: a clip art house)

```html
<!DOCTYPE html>
<html lang="en">
<head>
<meta charset="utf-8">
<title>Verano Estates – Business Card</title>
<link rel="stylesheet" href="https://fonts.googleapis.com/css2?family=Montserrat:wght@300;400;600&display=swap">
<style>
  :root {
    --stage: #3a3a3a;
    --stage-edge: #1b1b1b;
    --card: #2b2b2b;
    --card-back: #1f1f1f;
    --ink: #f2f2f2;
    --ink-soft: #cfcfcf;
    --silver: #d9d9d9;
    --accent-bar: #7a7a7a;
    --rule: #8c8c8c;
  }
  * { box-sizing: border-box; margin: 0; padding: 0; }
  html, body { width: 1200px; height: 900px; overflow: hidden; }
  body {
    background: radial-gradient(ellipse at 60% 45%, var(--stage) 0%, var(--stage-edge) 100%);
    font-family: "Montserrat", sans-serif;
    position: relative;
  }
  .card {
    position: absolute;
    top: 300px;
    width: 525px;
    height: 300px;
    border-radius: 22px;
    overflow: hidden;
    box-shadow: 0 18px 40px rgba(0,0,0,.55);
  }
  .card--front { left: 50px; background: var(--card); }
  .card--back { left: 625px; background: var(--card-back); }

  .brand {
    position: absolute;
    left: 30px; top: 80px;
    display: flex; align-items: center; gap: 14px;
  }
  .brand__mark {
    width: 46px; height: 46px;
    border: 2px solid var(--silver);
    border-radius: 50%;
    flex: none;
  }
  .brand__name {
    font-family: "Montserrat", sans-serif;
    font-weight: 400;
    font-size: 24px;
    line-height: 1.15;
    letter-spacing: 1.5px;
    color: var(--silver);
    text-transform: uppercase;
  }
  .divider {
    position: absolute;
    left: 262px; top: 60px;
    width: 1px; height: 112px;
    background: var(--rule);
  }
  .agent {
    position: absolute;
    left: 284px; top: 62px;
    color: var(--ink);
  }
  .agent__name { font-weight: 600; font-size: 19px; letter-spacing: .5px; text-transform: uppercase; }
  .agent__title { font-weight: 300; font-size: 12px; color: var(--ink-soft); margin: 2px 0 12px; }
  .contact { list-style: none; font-weight: 400; font-size: 13px; }
  .contact li { display: flex; align-items: center; gap: 8px; margin-bottom: 4px; }
  .contact svg { width: 11px; height: 11px; flex: none; }

  .tagline {
    position: absolute;
    left: 0; right: 0; bottom: 34px;
    display: flex; align-items: center; justify-content: space-between;
  }
  .tagline__bar { height: 7px; width: 72px; background: var(--accent-bar); flex: none; }
  .tagline__text {
    font-weight: 300; font-size: 14px; letter-spacing: .6px;
    color: var(--ink-soft); text-transform: uppercase; white-space: nowrap;
  }

  .back-pattern {
    position: absolute; inset: 0;
    background: radial-gradient(ellipse at 30% 30%, #2c2c2c 0%, var(--card-back) 70%);
  }
  .back-brand {
    position: absolute; left: 50%; top: 50%;
    transform: translate(-50%, -50%);
    display: flex; align-items: center; gap: 8px;
  }
  .back-brand__mark { width: 22px; height: 22px; border: 1.5px solid var(--silver); border-radius: 50%; flex: none; }
  .back-brand__name {
    font-family: "Montserrat", sans-serif; font-weight: 400;
    font-size: 13px; letter-spacing: 1.5px; color: var(--silver);
    text-transform: uppercase; white-space: nowrap;
  }
</style>
</head>
<body>
  <section class="card card--front">
    <div class="brand">
      <span class="brand__mark"></span>
      <span class="brand__name">Verano<br>Estates</span>
    </div>
    <div class="divider"></div>
    <div class="agent">
      <p class="agent__name">Daniel Reyes</p>
      <p class="agent__title">Director</p>
      <ul class="contact">
        <li>
          <svg viewBox="0 0 12 12"><path d="M2.5 1h2l1 3-1.3 1a6 6 0 0 0 2.8 2.8l1-1.3 3 1v2A1.5 1.5 0 0 1 9.5 11 8.5 8.5 0 0 1 1 2.5 1.5 1.5 0 0 1 2.5 1z" fill="#f2f2f2"/></svg>
          555.204.7719
        </li>
        <li>
          <svg viewBox="0 0 12 12"><rect x="1" y="2.5" width="10" height="7" rx="1" fill="none" stroke="#f2f2f2" stroke-width="1.2"/><path d="M1.5 3l4.5 3.5L10.5 3" fill="none" stroke="#f2f2f2" stroke-width="1.2"/></svg>
          hello@veranoestates.com
        </li>
        <li>
          <svg viewBox="0 0 12 12"><circle cx="6" cy="6" r="5" fill="none" stroke="#f2f2f2" stroke-width="1.2"/><path d="M1 6h10M6 1c-2.5 3-2.5 7 0 10M6 1c2.5 3 2.5 7 0 10" fill="none" stroke="#f2f2f2" stroke-width="1"/></svg>
          www.veranoestates.com
        </li>
      </ul>
    </div>
    <div class="tagline">
      <span class="tagline__bar"></span>
      <span class="tagline__text">Quietly Redefining Fine Homes</span>
      <span class="tagline__bar"></span>
    </div>
  </section>

  <section class="card card--back">
    <div class="back-pattern" role="img" aria-label="Repeating embossed brand pattern in gloss black on matte black"></div>
    <div class="back-brand">
      <span class="back-brand__mark"></span>
      <span class="back-brand__name">Verano Estates</span>
    </div>
  </section>
</body>
</html>
```